Flyer-Design für  junges, dynamisches Unternehmen, spezialisiert auf innovative Trainingskonzepte
Flyer-Design für junges, dynamisches Unternehmen, spezialisiert auf innovative Trainingskonzepte
volTEK
Sehr kreative und ideenreiche Umsetzungen. Alle Wünsche sind sehr sorgfältig, gewissenhaft und mit absoluter Schnelligkeit erfolgt.
Zielgruppe
Als junges dynamisches Unternehmen ist volTEK spezialisiert auf innovative Trainingskonzepte. Wir sind
ein international anerkanntes Trainingscenter der Northfield Rescue Council und bieten Notfalltrainings,
Erste-Hilfe-Kurse sowie hochwertige Simulationstrainings fur Rettungsdienste und Krankenhäuser an. In
unseren CRM- Simulationstrainings coachen wir Notfallteams in den Bereichen Skills, Human Factor und
Kommunikation. Hierbei kommen Full-Scale-Simulatoren und Schauspielpatienten zum Einsatz, die eine
realitätsnahe und lebensechte Trainingssituation präsentieren.
Aufgabenstellung
Wir suchen zur Vermarktung unserer Kurse eine graphische Übersicht, aus der die Qualitätsmerkmale von volTEK, eine Zielgruppen definition sowie eine detailierte Aufarbeitung der Kursinhalte in den Verschiedenen Kursformaten hervorgeht und unsere zukünftigen Kunden von uns überzeugt.
Großer Fokus dieses Projektes, ist es die Innenseite des Flyers zu gestalten, die ein geschlossenes Gesamtbild aufweisen soll. Deckblatt und Rückseite sind nebensächlich, hier freuen wir uns über neue Ideen, aber das Fokus ist die Gestaltung der Innenseite.

```html
<!DOCTYPE html>
<html lang="de">
<head>
<meta charset="utf-8">
<title>volTEK Flyer Notfalltraining</title>
<link href="https://fonts.googleapis.com/css2?family=Open+Sans:wght@400;600;700;800&display=swap" rel="stylesheet">
<style>
:root{
  --red:#d5182a;
  --ink:#3d3d3d;
  --grey-light:#e6e6e6;
  --grey-band:#cfcfcf;
  --paper:#ffffff;
  --stage:#eceef0;
  --photo-warm:#b9a79a;
  --photo-cool:#8e98a3;
}
*{box-sizing:border-box;margin:0;padding:0}
html,body{width:1200px;height:1200px;overflow:hidden}
body{background:var(--stage);font-family:"Open Sans",Arial,sans-serif;color:var(--ink);position:relative}
.spread{position:absolute;left:204px;width:792px;height:560px;display:flex;box-shadow:0 4px 18px rgba(0,0,0,.18)}
.spread--inside{top:26px}
.spread--outside{top:614px}
.page{position:relative;width:396px;height:560px;background:var(--paper);overflow:hidden}
.page + .page{border-left:1px solid #ddd}
.photo{position:absolute;background:linear-gradient(135deg,var(--photo-cool),var(--photo-warm))}
.photo--red{background:linear-gradient(160deg,#c8343d 0%,#b89f92 55%,#7d8590 100%)}
.swoosh{position:absolute;left:0;width:396px}
h2{font-size:10px;font-weight:700;color:var(--ink)}
h2 .brand{color:var(--red)}
h3{font-size:8px;font-weight:700;color:var(--red);margin-bottom:3px}
p,li{font-size:6px;line-height:1.45}
ul.dots{list-style:none}
ul.dots li{position:relative;padding-left:8px;margin-bottom:2px}
ul.dots li::before{content:"";position:absolute;left:0;top:2.5px;width:4px;height:4px;background:var(--red);border-radius:50%}
.advantages{position:absolute;left:22px;top:30px;width:352px}
.advantages p{margin:5px 0 6px}
.adv-list{width:200px}
.icons{position:absolute;left:240px;top:62px;width:112px;height:70px;border-radius:4px;background:linear-gradient(135deg,#f1d2d4,#e8e8e8)}
.who{position:absolute;left:22px;top:210px;width:150px}
.partner{display:flex;align-items:center;gap:5px;margin-top:8px}
.partner-badge{width:18px;height:18px;background:var(--red);border-radius:50%}
.partner-badge--sq{border-radius:2px;background:#2e6fb0}
.partner span{font-size:6px;font-weight:700;color:var(--ink)}
.courses{position:absolute;left:184px;top:210px;width:190px;border-left:2px solid var(--red);padding-left:8px}
.courses p{margin-bottom:4px}
.courses b{color:var(--red)}
.compare{position:absolute;left:18px;top:118px;width:360px}
.compare h2{font-size:11px;margin-bottom:5px}
table{width:100%;border-collapse:collapse;font-size:5.6px}
th{background:var(--red);color:#fff;font-weight:700;padding:3px 2px;text-align:center}
th:first-child{text-align:left}
td{padding:2.6px 2px;border-bottom:1px solid #fff;text-align:center}
td:first-child{text-align:left;width:46%}
tr:nth-child(odd) td{background:#f3e3e4}
tr:nth-child(even) td{background:#f7f7f7}
tr.section td{background:var(--grey-light);font-weight:700}
.tick{color:var(--red);font-weight:700}
tr.price td{background:var(--red);color:#fff;font-weight:700}
.claim{position:absolute;left:18px;top:470px;font-size:7px;font-weight:700;color:var(--red)}
.brand-name{position:absolute;font-weight:700;font-size:15px;color:var(--ink)}
.url{position:absolute;font-size:7px;font-weight:700;color:var(--red)}
.cover-bar{position:absolute;left:0;top:0;width:396px;height:30px;background:var(--red)}
.cover-bar .url{color:#fff;left:20px;top:10px}
.cover-title{position:absolute;left:98px;top:110px;width:290px;color:#fff;text-shadow:0 1px 3px rgba(0,0,0,.35)}
.cover-title h1{font-size:24px;font-weight:800;line-height:1}
.cover-title p{font-size:11px;line-height:1.25;margin-top:4px;font-weight:600}
.contact{position:absolute;left:24px;top:290px;width:348px}
.contact h2{color:var(--red);margin-bottom:6px}
.contact p{margin-bottom:6px}
.contact .line{font-size:7px;font-weight:600;display:flex;align-items:center;gap:6px;margin-bottom:3px}
.contact svg{width:9px;height:9px;fill:var(--red)}
.back-partners{position:absolute;left:24px;bottom:26px;display:flex;gap:14px}
</style>
</head>
<body>

<section class="spread spread--inside">
  <article class="page">
    <div class="advantages">
      <h2>Was zeichnet <span class="brand">volTEK</span> aus / Was sind unsere Vorteile?</h2>
      <p>Wir bieten ein breites Spektrum an Kursen und Workshops im Gesundheitsbereich an. Zur Zielgruppe unserer Angebote zählen Rettungsdienste, Kliniken, Arztpraxen und Firmen.</p>
      <ul class="dots adv-list">
        <li>Zertifizierte und erfahrene Instruktoren</li>
        <li>Realitätsnahe Szenarien mit Schauspielpatienten</li>
        <li>Modernste Simulatoren und Trainingstechnik</li>
        <li>Individuelle Kursinhalte für Ihr Team</li>
        <li>Video-Debriefing für nachhaltiges Lernen</li>
        <li>Schulungen vor Ort oder in unserem Zentrum</li>
        <li>Förderung der Teamarbeit durch CRM</li>
      </ul>
    </div>
    <div class="icons" role="img" aria-label="Kleine Illustrationen: Erste Hilfe, Personen und Notfallkoffer"></div>
    <div class="who">
      <h3>Wer wir sind:</h3>
      <ul class="dots">
        <li>International anerkanntes Trainingscenter der Northfield Rescue Council</li>
        <li>Partner und Förderer des Fachverband Simulation</li>
      </ul>
      <div class="partner"><div class="partner-badge"></div><span>Northfield Rescue Council</span></div>
      <div class="partner"><div class="partner-badge partner-badge--sq"></div><span>Fachverband Simulation</span></div>
    </div>
    <div class="courses">
      <h3>Unsere Kurse</h3>
      <p><b>Notfalltraining Light</b> – Lernen Sie in diesem Kurs die Grundlagen der Reanimation und der Frühdefibrillation mit dem AED.</p>
      <p><b>Notfalltraining Basis</b> – Intensives Training mit Feedback-Puppe. Sie üben die wichtigsten Handgriffe und lernen den sicheren Umgang mit dem Atemweg.</p>
      <p><b>Notfalltraining Premium</b> – Realistische Fallbeispiele an hochwertigen Simulatoren. Wir trainieren Teamarbeit und Kommunikation im Notfall.</p>
    </div>
    <div class="photo" style="left:0;top:372px;width:396px;height:188px" role="img" aria-label="Foto: Teilnehmer bei einem Simulationstraining im Schulungsraum"></div>
    <svg class="swoosh" style="top:340px" viewBox="0 0 396 70" height="70" aria-hidden="true">
      <path d="M0 0 H396 V22 C300 55 140 62 0 40 Z" fill="#fff"/>
      <path d="M0 40 C140 62 300 55 396 22 V30 C300 64 140 70 0 50 Z" fill="var(--red)"/>
    </svg>
  </article>

  <article class="page">
    <div class="photo" style="left:0;top:0;width:396px;height:108px" role="img" aria-label="Foto: Trainingsgruppe übt Reanimation an Übungspuppen"></div>
    <svg class="swoosh" style="top:84px" viewBox="0 0 396 30" height="30" aria-hidden="true">
      <path d="M0 30 C140 6 280 4 396 14 V30 Z" fill="#fff"/>
    </svg>
    <div class="compare">
      <h2>Unsere Kurse im Vergleich</h2>
      <table>
        <tr><th>Umfang</th><th>Light</th><th>Basis</th><th>Premium</th><th>Premium PLUS</th></tr>
        <tr><td>Dauer</td><td>2 Std.</td><td>3 Std.</td><td>4 Std.</td><td>6 Std.</td></tr>
        <tr><td>Teilnehmer</td><td>8</td><td>8</td><td>6</td><td>6</td></tr>
        <tr class="section"><td>Inhalte</td><td></td><td></td><td></td><td></td></tr>
        <tr><td>Basismaßnahmen der Reanimation</td><td class="tick">✓</td><td class="tick">✓</td><td class="tick">✓</td><td class="tick">✓</td></tr>
        <tr><td>Frühdefibrillation mit dem AED</td><td class="tick">✓</td><td class="tick">✓</td><td class="tick">✓</td><td class="tick">✓</td></tr>
        <tr><td>Reanimation mit Feedback-Puppe</td><td>–</td><td class="tick">✓</td><td class="tick">✓</td><td class="tick">✓</td></tr>
        <tr><td>Atemwegsmanagement Grundlagen</td><td>–</td><td class="tick">✓</td><td class="tick">✓</td><td class="tick">✓</td></tr>
        <tr><td>Training an hochwertigen Simulatoren</td><td>–</td><td class="tick">✓</td><td class="tick">✓</td><td class="tick">✓</td></tr>
        <tr><td>Übungen zu Kommunikation im Team</td><td>–</td><td>–</td><td class="tick">✓</td><td class="tick">✓</td></tr>
        <tr><td>Teamtraining nach CRM-Leitsätzen</td><td>–</td><td>–</td><td class="tick">✓</td><td class="tick">✓</td></tr>
        <tr><td>Fallbeispiele aus der Praxis</td><td>–</td><td>–</td><td class="tick">✓</td><td class="tick">✓</td></tr>
        <tr><td>Einsatz von Schauspielpatienten</td><td>–</td><td>–</td><td>–</td><td class="tick">✓</td></tr>
        <tr><td>Strukturiertes Video-Debriefing</td><td>–</td><td>–</td><td>–</td><td class="tick">✓</td></tr>
        <tr class="price"><td>Preis pro Person</td><td>12,- €</td><td>25,- €</td><td>45,- €</td><td>78,- €</td></tr>
      </table>
    </div>
    <div class="claim">Wir bieten Ihnen ein modernes Training unter Einsatz von Video-Debriefing!</div>
    <span class="brand-name" style="right:22px;bottom:40px">volTEK</span>
    <div class="url" style="right:22px;bottom:22px">www.voltek-training.de</div>
  </article>
</section>

<section class="spread spread--outside">
  <article class="page">
    <div class="photo" style="left:0;top:0;width:396px;height:250px" role="img" aria-label="Foto: Teilnehmer bei der Nachbesprechung eines Simulationstrainings"></div>
    <svg class="swoosh" style="top:218px" viewBox="0 0 396 40" height="40" aria-hidden="true">
      <path d="M0 40 C130 10 280 4 396 20 V40 Z" fill="#fff"/>
    </svg>
    <div class="contact">
      <h2>Wir finden das richtige Training für Sie!</h2>
      <p>Sprechen Sie uns mit Ihren Anfragen sowie persönlichen Wünschen an und wir erstellen Ihnen gerne ein Angebot für Ihre maßgeschneiderten Kurse.</p>
      <p><b>Inhouse-Schulung</b> – Wir kommen mit unseren Simulatoren zu Ihnen in die Einrichtung, Firma oder Klinik. Rufen Sie uns einfach an.</p>
      <div class="line"><svg viewBox="0 0 10 10"><path d="M2 0h2l1 3-1.5 1a6 6 0 0 0 2.5 2.5L7 5l3 1v2a2 2 0 0 1-2 2A8 8 0 0 1 0 2a2 2 0 0 1 2-2z"/></svg>Telefon: 0421 / 36 14 29</div>
      <div class="line"><svg viewBox="0 0 10 10"><path d="M0 2h10v6H0z"/></svg>info@voltek-training.de</div>
      <div class="line"><svg viewBox="0 0 10 10"><circle cx="5" cy="5" r="5"/></svg>www.voltek-training.de</div>
    </div>
    <div class="back-partners">
      <div class="partner"><div class="partner-badge"></div><span>Northfield Rescue Council</span></div>
      <div class="partner"><div class="partner-badge partner-badge--sq"></div><span>Training Center</span></div>
    </div>
  </article>

  <article class="page">
    <div class="photo photo--red" style="left:0;top:30px;width:396px;height:370px" role="img" aria-label="Foto: Herzdruckmassage an einer Übungspuppe mit blauen Handschuhen"></div>
    <div class="cover-bar"><span class="url">www.voltek-training.de</span></div>
    <div class="cover-title">
      <h1>Notfalltraining</h1>
      <p>Professionell und praxisnah –<br>damit Sie gut vorbereitet sind.</p>
    </div>
    <svg class="swoosh" style="top:350px" viewBox="0 0 396 90" height="90" aria-hidden="true">
      <path d="M0 60 C150 20 300 10 396 30 V90 H0 Z" fill="#fff"/>
      <path d="M0 48 C150 10 300 0 396 18 V30 C300 10 150 20 0 60 Z" fill="var(--grey-band)"/>
      <path d="M0 40 C150 2 300 -6 396 8 V18 C300 0 150 10 0 48 Z" fill="var(--red)"/>
    </svg>
    <span class="brand-name" style="right:24px;bottom:38px">volTEK</span>
  </article>
</section>

</body>
</html>
```